KAJU Freightways #ALLKAJU Business Cards & Letterhead

I am looking to business cards designed for our organization. We are currently undergoing a small re-branding that is taking place. Our organization is called KAJU Freightways and we are headquartered in Phoenix, AZ. We primarily provide transportation and logistics services to the Marlow Parcel Bureau who is our largest customer. I would like to see a design that incorporates name, title, contact info, website, and address (this will be different depending on the employee). I would also like to see some color on the business card using our logo colors or a variation. I would like our logo on the back of the business card with the website displayed. The final design should communicate that we are a next generation transportation operate that focuses on being driver-first, customer-centric, innovative, and sustainable.We would also like our #ALLKAJU catch phrase incorporated as well.

Target Market(s)

Transportation & Logistics

Industry/Entity Type

Trucking Company

Contact Information for Business Card

-First and Last Name
-Position Title
-Contact Phone
-Contact Email
-Physical Address

Font styles to use
Serif

Colors

Designer to choose colors to be used in the design.

Requirements
Must have
• -KAJU logo prominently displayed
• -#ALLKAJU catch phrase used
• -Some amount of color, design gradient, etc.
• -Logo on the back with website listed (https://www.kajufreightco.example)

```html
<!DOCTYPE html>
<html lang="en">
<head>
<meta charset="utf-8">
<title>KAJU Freightways Business Card</title>
<link href="https://fonts.googleapis.com/css2?family=Roboto:wght@300;400;500&display=swap" rel="stylesheet">
<style>
  :root {
    --backdrop: #d9d9d9;
    --navy: #033a47;
    --green: #83c441;
    --white: #ffffff;
  }
  html, body {
    margin: 0;
    padding: 0;
    width: 1125px;
    height: 1200px;
    overflow: hidden;
    background: var(--backdrop);
  }
  .canvas {
    position: relative;
    width: 1125px;
    height: 1200px;
    font-family: "Roboto", Arial, sans-serif;
  }
  .card {
    position: absolute;
    left: 150px;
    width: 826px;
    height: 472px;
    display: block;
  }
  .card-front { top: 98px; }
  .card-back { top: 631px; }
  .brand-name { font-weight: 500; letter-spacing: 1px; }
  .person-name { font-weight: 500; fill: var(--green); }
  .person-title { font-weight: 300; fill: var(--white); }
  .contact-line { font-weight: 300; fill: var(--white); }
  .contact-accent { fill: var(--green); }
  .address-line { font-weight: 300; fill: var(--white); }
  .tagline { font-weight: 500; fill: var(--white); letter-spacing: 3px; }
  .back-website { font-weight: 300; fill: var(--white); letter-spacing: 1px; }
</style>
</head>
<body>
<main class="canvas">

  <svg class="card card-front" viewBox="0 0 800 457" aria-label="Business card front">
    <defs>
      <clipPath id="front-shape"><rect width="800" height="457" rx="20"/></clipPath>
    </defs>
    <g clip-path="url(#front-shape)">
      <rect class="front-base" width="800" height="457" fill="var(--white)"/>

      <g class="brand-mark">
        <circle cx="400" cy="142" r="102" fill="none" stroke="var(--green)" stroke-width="6"/>
        <text class="brand-name" x="400" y="163" text-anchor="middle" font-size="56" fill="var(--navy)">KAJU</text>
      </g>

      <rect class="accent-rule" y="272" width="800" height="6" fill="var(--green)"/>
      <rect class="info-band" y="281" width="800" height="124" fill="var(--navy)"/>
      <rect class="address-band" y="410" width="800" height="47" fill="var(--green)"/>

      <text class="person-name" x="358" y="341" text-anchor="end" font-size="28">Mara Keller</text>
      <text class="person-title" x="358" y="366" text-anchor="end" font-size="20">Manager</text>

      <line class="info-divider" x1="393" y1="303" x2="393" y2="383" stroke="var(--white)" stroke-width="1"/>

      <g class="contact-icons" fill="var(--green)">
        <path class="icon-phone" d="M425 310 q2 -2 4 0 l2 3 q1 2 -1 3 l-1 1 q2 4 6 6 l1 -1 q1 -2 3 -1 l3 2 q2 2 0 4 l-2 1 q-6 1 -12 -6 q-5 -6 -5 -11 z"/>
        <g class="icon-mail">
          <rect x="424" y="338" width="16" height="11" rx="1"/>
          <polyline points="424,338 432,345 440,338" fill="none" stroke="var(--navy)" stroke-width="1.5"/>
        </g>
        <g class="icon-web">
          <circle cx="432" cy="368" r="8"/>
          <path d="M424 368 h16 M432 360 q-5 8 0 16 M432 360 q5 8 0 16" fill="none" stroke="var(--navy)" stroke-width="1.3"/>
        </g>
      </g>

      <text class="contact-line" x="452" y="325" font-size="19.5">623-555-0148</text>
      <text class="contact-line" x="452" y="350" font-size="19.5">info@kajufreightco.example</text>
      <text class="contact-line" x="452" y="375" font-size="19.5">www.<tspan class="contact-accent">kajufreightco</tspan>.example</text>

      <text class="address-line" x="400" y="440" text-anchor="middle" font-size="20">4410 North Canyon Ridge Road, Phoenix, AZ 85016</text>
    </g>
  </svg>

  <svg class="card card-back" viewBox="0 0 800 457" aria-label="Business card back">
    <defs>
      <clipPath id="back-shape"><rect width="800" height="457" rx="20"/></clipPath>
      <radialGradient id="map-tint" cx="50%" cy="45%" r="60%">
        <stop offset="0%" stop-color="#8fcb52"/>
        <stop offset="100%" stop-color="#83c441"/>
      </radialGradient>
    </defs>
    <g clip-path="url(#back-shape)">
      <rect class="back-base" width="800" height="457" fill="var(--green)"/>
      <rect class="world-map-area" x="10" y="5" width="780" height="440" fill="url(#map-tint)" role="img" aria-label="Faint dotted world map in a lighter green"/>
      <g class="brand-mark">
        <circle cx="400" cy="210" r="127" fill="none" stroke="var(--white)" stroke-width="7"/>
        <text class="brand-name" x="400" y="236" text-anchor="middle" font-size="70" fill="var(--white)">KAJU</text>
      </g>
      <text class="tagline" x="400" y="382" text-anchor="middle" font-size="20">#ALLKAJU</text>
      <text class="back-website" x="400" y="415" text-anchor="middle" font-size="17">www.kajufreightco.example</text>
    </g>
  </svg>

</main>
</body>
</html>
```